Brook Refrigeration. Refrigeration and air conditioning specialists.

We need a website to promote our business. We would a modern simple design using the colours from our logo and black. We want it to be fun but proffesional.

Target Market(s)

Commercial

Number of Pages Required

4 page

Requirements
Must have
• Home Page, About Us, Services and Contact Us.
• 24/7 365 days service available.
• Brook Refrigeration's dedicated team specialises in commercial refrigeration and air conditioning equipment.
• Based in Joondalup, we cover Perth Metro and surrounding areas.
Nice to have
• KNOWLEDGE . EXPERIENCE . PASSION in bold.
• Our experienced and highly trained technicians provide extensive knowledge and exceptional skills for your commercial refrigeration and air conditioning requirements.
• Pictures of commercial refrigeration.
Should not have
• No mention of domestic services.

```html
<!DOCTYPE html>
<html lang="en">
<head>
<meta charset="utf-8">
<title>Brook Refrigeration</title>
<link href="https://fonts.googleapis.com/css2?family=Lato:wght@400;700;900&display=swap" rel="stylesheet">
<style>
:root{
  --green:#9bf55c;
  --purple:#2c1a4c;
  --ink:#1a1a1a;
  --body:#555;
  --grey-band:#f0f0f0;
  --white:#fff;
}
*{box-sizing:border-box;margin:0;padding:0}
html,body{width:1200px;height:3383px;overflow:hidden}
body{font-family:'Lato',sans-serif;color:var(--ink);background:var(--white);position:relative}
.abs{position:absolute}
.site-header{position:absolute;left:0;top:0;width:1200px;height:171px;background:var(--white)}
.brand{position:absolute;left:77px;top:52px;display:flex;align-items:center;gap:14px;font-weight:900;font-size:30px;color:var(--green);line-height:1}
.brand-square{width:44px;height:44px;background:var(--green)}
.follow-top{position:absolute;left:657px;top:46px;display:flex;align-items:center;gap:14px;font-size:14px;font-weight:700}
.dot-icon{width:16px;height:16px;border-radius:50%;background:var(--ink);display:inline-block}
.phone-top{position:absolute;left:860px;top:42px;display:flex;align-items:center;gap:12px;font-size:23px;font-weight:700}
.badge-24{position:absolute;left:1069px;top:27px;width:56px;height:56px;border:4px solid var(--purple);border-radius:50%;display:flex;align-items:center;justify-content:center;font-weight:900;font-size:16px;color:var(--purple)}
.main-nav{position:absolute;top:117px;right:74px;display:flex;gap:0;font-size:15px;font-weight:700}
.main-nav a{display:block;padding:0 20px;height:36px;line-height:36px;color:var(--ink);text-decoration:none}
.main-nav a.active{background:var(--green)}
.hero{position:absolute;left:0;top:171px;width:1200px;height:562px;background:linear-gradient(180deg,#c9c9c7 0%,#a9a8a4 45%,#8d8b86 100%)}
.hero-text{position:absolute;left:0;top:330px;width:1200px;text-align:center;color:var(--white)}
.hero-text .lead{font-size:30px;font-weight:700}
.hero-text h1{font-size:39px;font-weight:900;line-height:44px;margin-top:6px}
.hero-text .tagline{font-size:29px;font-weight:900;color:var(--green);margin-top:10px;letter-spacing:1px}
.btn{display:inline-block;background:var(--green);color:var(--ink);font-weight:700;font-size:15px;text-align:center;text-decoration:none}
.hero .btn{position:absolute;left:525px;top:350px;width:150px;height:41px;line-height:41px}
.hero-dots{position:absolute;left:560px;top:518px;display:flex;gap:10px}
.hero-dots span{width:10px;height:10px;border-radius:50%;background:var(--white)}
.hero-dots span.on{background:var(--green)}
.section-title{position:absolute;border:3px solid var(--purple);font-weight:900;font-size:29px;color:var(--purple);text-align:center;display:flex;align-items:center;justify-content:center}
.section-title em{font-style:normal;color:var(--green)}
.about-text{position:absolute;left:60px;top:880px;width:1080px;text-align:center;font-size:21px;line-height:34px;color:var(--body);letter-spacing:.3px}
.services-band{position:absolute;left:0;top:1090px;width:1200px;height:920px;background:var(--grey-band)}
.photo{position:absolute}
.service-copy{position:absolute;width:490px}
.service-copy h2{font-size:28px;font-weight:900;color:var(--purple)}
.service-copy p{font-size:15px;line-height:23px;color:var(--body);margin-top:16px}
.offer-col{position:absolute;top:2160px;width:320px;text-align:center}
.offer-col svg{display:block;margin:0 auto}
.offer-col h3{font-size:25px;font-weight:900;color:var(--purple);margin-top:36px}
.offer-col p{font-size:15px;line-height:23px;color:var(--body);margin-top:12px}
.contact-band{position:absolute;left:0;top:2475px;width:1200px;height:652px;background:var(--green)}
.contact-intro{position:absolute;left:0;top:2628px;width:1200px;text-align:center;font-size:19px;font-weight:700;line-height:29px;color:var(--purple)}
.field{position:absolute;background:var(--white);font-size:14px;color:#444;padding:16px 16px}
.submit{position:absolute;left:523px;top:3012px;width:152px;height:45px;background:var(--purple);color:var(--white);font-weight:700;font-size:15px;text-align:center;line-height:45px}
.footer-brand{position:absolute;left:74px;top:3192px;display:flex;align-items:center;gap:10px;font-weight:900;font-size:22px;color:var(--green)}
.footer-brand .brand-square{width:30px;height:30px}
.legal{position:absolute;left:74px;top:3276px;font-size:12px;line-height:23px;color:var(--body)}
.foot-col{position:absolute;top:3180px}
.foot-col h4{font-size:14px;font-weight:900;color:var(--purple);margin-bottom:10px}
.foot-col li{list-style:none;font-size:13px;line-height:27px;color:var(--ink)}
.foot-contact li{display:flex;align-items:center;gap:16px}
.foot-follow{display:flex;gap:18px;margin-top:16px}
</style>
</head>
<body>

<header class="site-header">
  <div class="brand"><span class="brand-square"></span>Brook Refrigeration</div>
  <div class="follow-top">FOLLOW US <span class="dot-icon"></span><span class="dot-icon"></span></div>
  <div class="phone-top">
    <svg width="20" height="20" viewBox="0 0 24 24"><path fill="#1a1a1a" d="M6.6 10.8a15.1 15.1 0 0 0 6.6 6.6l2.2-2.2c.3-.3.7-.4 1-.2 1.1.4 2.3.6 3.6.6.6 0 1 .4 1 1V20c0 .6-.4 1-1 1A17 17 0 0 1 3 4c0-.6.4-1 1-1h3.5c.6 0 1 .4 1 1 0 1.3.2 2.5.6 3.6.1.3 0 .7-.2 1z"/></svg>
    1300-555-014
  </div>
  <div class="badge-24">24</div>
  <nav class="main-nav">
    <a class="active" href="#">HOME</a><a href="#">ABOUT</a><a href="#">SERVICES</a><a href="#">WHAT WE OFFER</a><a href="#">CONTACT</a>
  </nav>
</header>

<section class="hero" role="img" aria-label="Photo of an empty commercial cool room with steel shelving and ceiling evaporator units">
  <div class="hero-text" style="top:160px">
    <p class="lead">Our dedicated team specialises in</p>
    <h1>COMMERCIAL REFRIGERATION &amp;<br>AIR CONDITIONING EQUIPMENT</h1>
    <p class="tagline">KNOWLEDGE . EXPERIENCE . PASSION</p>
  </div>
  <a class="btn" href="#">READ MORE</a>
  <div class="hero-dots"><span class="on"></span><span></span><span></span><span></span></div>
</section>

<div class="section-title" style="left:374px;top:801px;width:452px;height:61px">ABOUT&nbsp;<em>BROOK</em>&nbsp;REFRIGERATION</div>
<p class="about-text">Brook Refrigeration are commercial refrigeration and air conditioning specialists providing a comprehensive service throughout the Perth Metro area - 24 hours / 7 days a week</p>
<a class="btn abs" href="#" style="left:525px;top:986px;width:150px;height:43px;line-height:43px">READ MORE</a>

<section class="services-band"></section>
<div class="section-title" style="left:478px;top:1132px;width:244px;height:61px">OUR SERVICES</div>

<div class="photo" role="img" aria-label="Photo of a supermarket aisle lined with glass-door display fridges" style="left:74px;top:1245px;width:526px;height:350px;background:linear-gradient(180deg,#c8232b 0%,#b8b9b3 35%,#d8d6cf 70%,#bdb7ac 100%)"></div>
<div class="service-copy" style="left:638px;top:1288px">
  <h2>COMMERCIAL REFRIGERATION</h2>
  <p>Lorem ipsum dolor sit amet, consectetur adipiscing elit. In ut leo sit amet mauris pellentesque lobortis. Praesent vulputate dictum venenatis. Pellentesque habitant morbi tristique senectus et netus et malesuada fames ac turpis egestas. Quisque sodales, dolor non convallis condimentum, arcu diam feugiat ligula...</p>
</div>
<a class="btn abs" href="#" style="left:638px;top:1498px;width:152px;height:45px;line-height:45px">READ MORE</a>

<div class="service-copy" style="left:74px;top:1655px">
  <h2>AIR CONDITIONING EQUIPMENT</h2>
  <p>Lorem ipsum dolor sit amet, consectetur adipiscing elit. In ut leo sit amet mauris pellentesque lobortis. Praesent vulputate dictum venenatis. Pellentesque habitant morbi tristique senectus et netus et malesuada fames ac turpis egestas. Quisque sodales, dolor non convallis condimentum, arcu diam feugiat ligula...</p>
</div>
<a class="btn abs" href="#" style="left:74px;top:1863px;width:152px;height:43px;line-height:43px">READ MORE</a>
<div class="photo" role="img" aria-label="Photo of a row of outdoor air conditioning condenser units against a wall" style="left:600px;top:1597px;width:526px;height:348px;background:linear-gradient(180deg,#e6e8ea 0%,#c2c6ca 45%,#3a4a5e 75%,#9a9fa3 100%)"></div>

<div class="section-title" style="left:447px;top:2062px;width:306px;height:61px">WHAT WE OFFER</div>

<div class="offer-col" style="left:81px">
  <svg width="100" height="100" viewBox="0 0 100 100" aria-hidden="true">
    <rect x="20" y="40" width="44" height="40" rx="8" fill="#9bf55c" stroke="#2c1a4c" stroke-width="3"/>
    <rect x="10" y="46" width="14" height="34" fill="#9bf55c" stroke="#2c1a4c" stroke-width="3"/>
    <circle cx="70" cy="26" r="13" fill="none" stroke="#2c1a4c" stroke-width="4"/>
    <line x1="62" y1="36" x2="48" y2="52" stroke="#2c1a4c" stroke-width="6" stroke-linecap="round"/>
  </svg>
  <h3>SERVICE</h3>
  <p>Lorem ipsum dolor sit amet, consectetur adipiscing elit. In ut leo sit amet mauris pellentesque lobortis. Nam id purus nec turpis ullamcorper laoreet sed ut ex.</p>
</div>
<div class="offer-col" style="left:440px">
  <svg width="100" height="100" viewBox="0 0 100 100" aria-hidden="true" stroke="#2c1a4c" stroke-width="4" stroke-linecap="round">
    <line x1="50" y1="8" x2="50" y2="92" stroke="#9bf55c" stroke-width="8"/>
    <line x1="14" y1="29" x2="86" y2="71" stroke="#9bf55c" stroke-width="8"/>
    <line x1="14" y1="71" x2="86" y2="29" stroke="#9bf55c" stroke-width="8"/>
    <line x1="50" y1="8" x2="50" y2="92"/><line x1="14" y1="29" x2="86" y2="71"/><line x1="14" y1="71" x2="86" y2="29"/>
    <polyline points="40,14 50,24 60,14" fill="none"/><polyline points="40,86 50,76 60,86" fill="none"/>
  </svg>
  <h3>MAINTENANCE</h3>
  <p>Lorem ipsum dolor sit amet, consectetur adipiscing elit. In ut leo sit amet mauris pellentesque lobortis. Nam id purus nec turpis ullamcorper laoreet sed ut ex.</p>
</div>
<div class="offer-col" style="left:799px">
  <svg width="100" height="100" viewBox="0 0 100 100" aria-hidden="true">
    <rect x="26" y="4" width="36" height="90" rx="3" fill="#9bf55c" stroke="#2c1a4c" stroke-width="3"/>
    <line x1="26" y1="34" x2="62" y2="34" stroke="#2c1a4c" stroke-width="3"/>
    <circle cx="64" cy="70" r="20" fill="#fff" stroke="#2c1a4c" stroke-width="3"/>
    <line x1="54" y1="60" x2="74" y2="80" stroke="#2c1a4c" stroke-width="4"/>
    <line x1="74" y1="60" x2="54" y2="80" stroke="#2c1a4c" stroke-width="4"/>
  </svg>
  <h3>REPAIR</h3>
  <p>Lorem ipsum dolor sit amet, consectetur adipiscing elit. In ut leo sit amet mauris pellentesque lobortis. Nam id purus nec turpis ullamcorper laoreet sed ut ex.</p>
</div>

<section class="contact-band"></section>
<div class="section-title" style="left:447px;top:2542px;width:306px;height:61px">CONATCT US</div>
<p class="contact-intro">Contact us on 1300 555 014 for out of hours emergencies<br>Or leave us a message.</p>
<div class="field" style="left:226px;top:2711px;width:361px;height:50px">Name</div>
<div class="field" style="left:614px;top:2711px;width:360px;height:50px">Phone Name</div>
<div class="field" style="left:226px;top:2777px;width:748px;height:52px">Email Address</div>
<div class="field" style="left:226px;top:2845px;width:748px;height:135px">Message</div>
<div class="submit">SUBMIT</div>

<footer>
  <div class="footer-brand"><span class="brand-square"></span>Brook Refrigeration</div>
  <div class="legal">Copyright © 2018 Brook Refrigeration Pty Ltd.<br>All Rights Reserved.<br>ABN 00 111 222 333.</div>
  <div class="foot-col" style="left:415px">
    <h4>SITE MAP</h4>
    <ul><li>Home</li><li>About</li><li>Services</li><li>What We Offer</li><li>Contact Us</li></ul>
  </div>
  <div class="foot-col foot-contact" style="left:627px">
    <h4>CONTACT US</h4>
    <ul>
      <li><svg width="14" height="14" viewBox="0 0 24 24"><path fill="#1a1a1a" d="M6.6 10.8a15.1 15.1 0 0 0 6.6 6.6l2.2-2.2c.3-.3.7-.4 1-.2 1.1.4 2.3.6 3.6.6.6 0 1 .4 1 1V20c0 .6-.4 1-1 1A17 17 0 0 1 3 4c0-.6.4-1 1-1h3.5c.6 0 1 .4 1 1 0 1.3.2 2.5.6 3.6.1.3 0 .7-.2 1z"/></svg>1-800-555-0199</li>
      <li><svg width="14" height="12" viewBox="0 0 24 20"><rect x="1" y="2" width="22" height="16" fill="#1a1a1a"/><polyline points="1,2 12,11 23,2" fill="none" stroke="#fff" stroke-width="2"/></svg>info@brookrefrig.example</li>
    </ul>
  </div>
  <div class="foot-col" style="left:907px">
    <h4>FOLLOW US</h4>
    <div class="foot-follow"><span class="dot-icon"></span><span class="dot-icon"></span></div>
  </div>
</footer>

</body>
</html>
```